Business Card Design

We need a business card designed for our new company. Prefer a black card with white logo & writing.

Contact Information for Business Card

Ted Galloway, address: 7-4812 Fernhollow Road, Abbotsford, BC, V3K 8R2, Office Phone: 604-712-3390, Cell: 604-947-2164, Email: ted@resinworkshub.ca

Colors

Designer to choose only greyscale colors for use in the design.

```html
<!DOCTYPE html>
<html lang="en">
<head>
<meta charset="utf-8">
<title>Resinworks Hub – Business Card</title>
<link href="https://fonts.googleapis.com/css2?family=Figtree:wght@400;700&display=swap" rel="stylesheet">
<style>
  :root {
    --stage: #1f1f1f;
    --card: #000000;
    --ink: #ffffff;
    --ink-soft: #e6e6e6;
  }
  * { margin: 0; padding: 0; box-sizing: border-box; }
  html, body { width: 1200px; height: 900px; overflow: hidden; }
  body {
    background: var(--stage);
    font-family: "Figtree", Arial, sans-serif;
    color: var(--ink);
    position: relative;
  }
  .card {
    position: absolute;
    left: 341px;
    width: 518px;
    height: 296px;
    background: var(--card);
  }
  .card--front { top: 141px; }
  .card--back { top: 463px; }

  .brand-mark {
    position: absolute;
    display: flex;
    align-items: center;
    gap: 6px;
    font-weight: 700;
    color: var(--ink);
    letter-spacing: 0.02em;
    white-space: nowrap;
  }
  .brand-mark__square {
    display: block;
    background: var(--ink);
  }
  .card--front .brand-mark {
    right: 26px;
    top: 33px;
    font-size: 11px;
  }
  .card--front .brand-mark__square { width: 8px; height: 8px; }

  .card--back .brand-mark {
    left: 50%;
    top: 50%;
    transform: translate(-50%, -50%);
    font-size: 34px;
    gap: 14px;
  }
  .card--back .brand-mark__square { width: 22px; height: 22px; }

  .person {
    position: absolute;
    right: calc(518px - 220px);
    top: 128px;
    text-align: right;
  }
  .person__name {
    font-size: 18px;
    font-weight: 700;
    letter-spacing: 0.01em;
    line-height: 1;
  }
  .person__role {
    font-size: 13px;
    color: var(--ink-soft);
    margin-top: 5px;
  }
  .divider {
    position: absolute;
    left: 238px;
    top: 115px;
    width: 1.5px;
    height: 66px;
    background: var(--ink);
  }
  .contact-list {
    position: absolute;
    left: 256px;
    top: 113px;
    list-style: none;
  }
  .contact-list__item {
    display: flex;
    align-items: center;
    height: 18px;
    font-size: 13.5px;
    color: var(--ink);
  }
  .contact-list__icon {
    width: 12px;
    height: 12px;
    margin-right: 5px;
    fill: var(--ink);
    flex: none;
  }
  .address {
    position: absolute;
    left: 0;
    right: 0;
    top: 258px;
    text-align: center;
    font-size: 13.5px;
  }
</style>
</head>
<body>
  <section class="card card--front" aria-label="Card front">
    <div class="brand-mark"><span class="brand-mark__square"></span>RESINWORKS HUB</div>

    <div class="person">
      <div class="person__name">TED GALLOWAY</div>
      <div class="person__role">President</div>
    </div>

    <div class="divider"></div>

    <ul class="contact-list">
      <li class="contact-list__item">
        <svg class="contact-list__icon" viewBox="0 0 24 24"><path d="M6.6 10.8a15.1 15.1 0 0 0 6.6 6.6l2.2-2.2c.3-.3.7-.4 1-.2 1.1.4 2.3.6 3.6.6.6 0 1 .4 1 1V20c0 .6-.4 1-1 1A17 17 0 0 1 3 4c0-.6.4-1 1-1h3.5c.6 0 1 .4 1 1 0 1.3.2 2.5.6 3.6.1.3 0 .7-.2 1z"/></svg>
        604-712-3390
      </li>
      <li class="contact-list__item">
        <svg class="contact-list__icon" viewBox="0 0 24 24"><path d="M7 1h10a2 2 0 0 1 2 2v18a2 2 0 0 1-2 2H7a2 2 0 0 1-2-2V3a2 2 0 0 1 2-2zm0 3v15h10V4zm5 16.2a1 1 0 1 0 0 .1z"/></svg>
        604-947-2164
      </li>
      <li class="contact-list__item">
        <svg class="contact-list__icon" viewBox="0 0 24 24"><path d="M2 5h20v2.2l-10 6.2L2 7.2zm0 4.5 10 6.2 10-6.2V19H2z"/></svg>
        ted@resinworkshub.ca
      </li>
      <li class="contact-list__item">
        <svg class="contact-list__icon" viewBox="0 0 24 24"><path d="M12 2a10 10 0 1 0 0 20 10 10 0 0 0 0-20zm6.9 9h-3a15 15 0 0 0-1.3-5.9A8 8 0 0 1 18.9 11zM12 4.1c.9 1.2 1.8 3.6 1.9 6.9h-3.8c.1-3.3 1-5.7 1.9-6.9zM9.4 5.1A15 15 0 0 0 8.1 11h-3a8 8 0 0 1 4.3-5.9zM5.1 13h3a15 15 0 0 0 1.3 5.9A8 8 0 0 1 5.1 13zm6.9 6.9c-.9-1.2-1.8-3.6-1.9-6.9h3.8c-.1 3.3-1 5.7-1.9 6.9zm2.6-1a15 15 0 0 0 1.3-5.9h3a8 8 0 0 1-4.3 5.9z"/></svg>
        resinworkshub.ca
      </li>
    </ul>

    <p class="address">7-4812 Fernhollow Road, Abbotsford, BC, V3K 8R2</p>
  </section>

  <section class="card card--back" aria-label="Card back">
    <div class="brand-mark"><span class="brand-mark__square"></span>RESINWORKS HUB</div>
  </section>
</body>
</html>
```